Steady Hands, professional newsletter for GAPM

** updated based on results so far** We need a 2 page newsletter designed on both sides of an 8.6 x 11 sheet back and front. Page one needs our logo below, name steady hands in large letters tagline of official newsletter of the guild of acute practice medicine volume and issue number locations It needs to include five locations for 250-400 word articles each with a spot for a picture. Page 2 needs to include contact information including address, phone number, email, twitter and facebook info below. The design need to complement out log in color, be professional with clean lines and easy to follow. We are a non profit organization dedicated to providers of urgent care medicine.

Target Market(s)

Physicians, Nurse Practitioners, Physician Assistants

Requirements
Must have
• 2 pages, back and front 8.5x 11
• 5 article area 250-400 words, one image for each
• our logo
• Name: Steady Hands - page one large visible print
• Contact inf:
• Guild of Acute Practice Medicine
• 912 Larkmoor Ave. Suite 418E
• Naperville, IL 60563
• 1 855-314-7093
• Info@gaopm.org
• @GuildAPM
Nice to have
• ease of entering info
• professional clean lines

```html
<!DOCTYPE html>
<html lang="en">
<head>
<meta charset="utf-8">
<title>Steady Hands — Inner Pages</title>
<link rel="stylesheet" href="https://fonts.googleapis.com/css2?family=Open+Sans:wght@400;600&family=PT+Sans+Narrow:wght@400;700&display=swap">
<style>
  :root {
    --backdrop: #ece4e5;
    --paper: #f4f4f4;
    --paper-edge: #ececec;
    --amber: #e8a033;
    --brick: #ad3b28;
    --photo-blue: #3b74b3;
    --ink: #4a4a4a;
    --heading: #3a3a3a;
    --white: #ffffff;
  }
  * { box-sizing: border-box; margin: 0; padding: 0; }
  html, body { width: 1200px; height: 1200px; overflow: hidden; }
  body {
    background: var(--backdrop);
    font-family: "Open Sans", Arial, sans-serif;
    color: var(--ink);
    position: relative;
  }
  .spread {
    position: absolute;
    left: 40px; top: 192px;
    width: 1120px; height: 815px;
    display: flex;
  }
  .page {
    position: relative;
    width: 560px; height: 815px;
    background: linear-gradient(90deg, var(--paper) 0%, #f7f7f7 60%, var(--paper-edge) 100%);
    overflow: hidden;
  }
  .page--right {
    background: linear-gradient(90deg, var(--paper-edge) 0%, #f7f7f7 40%, var(--paper) 100%);
    border-left: 1px solid #e0e0e0;
  }
  .page__top-band {
    position: absolute; left: 0; right: 0; top: 0;
    height: 13px; background: var(--amber);
  }
  .page__body {
    position: absolute;
    top: 34px; bottom: 40px;
    left: 31px; right: 34px;
  }
  .page--right .page__body { left: 36px; right: 33px; top: 34px; }
  .page__body p {
    font-size: 8.3px;
    line-height: 12.6px;
    text-align: justify;
    margin-bottom: 12.6px;
    hyphens: auto;
  }
  .article-title {
    font-family: "PT Sans Narrow", "Arial Narrow", sans-serif;
    font-weight: 700;
    font-size: 13px;
    letter-spacing: 0.1px;
    color: var(--heading);
    margin-bottom: 6px;
  }
  .intro { margin-bottom: 30px; }
  .photo-slot {
    background: var(--photo-blue);
    color: var(--white);
    display: flex; flex-direction: column;
    align-items: center; justify-content: center;
    text-align: center;
  }
  .photo-slot__label {
    font-family: "PT Sans Narrow", "Arial Narrow", sans-serif;
    font-weight: 700; font-size: 22px; line-height: 1;
  }
  .photo-slot__sub {
    font-size: 12px; line-height: 1.3; opacity: 0.8;
  }
  .photo-slot--right { float: right; margin: 0 0 8px 8px; }
  .photo-slot--left { float: left; margin: 2px 10px 8px 0; }
  .photo-slot--a { width: 234px; height: 204px; }
  .photo-slot--b { width: 240px; height: 194px; }
  .photo-slot--c { width: 261px; height: 184px; }
  .clear { clear: both; }

  .page__footer {
    position: absolute; left: 0; right: 0; bottom: 0;
    height: 16px; background: var(--amber);
  }
  .page--left .page__footer { right: 3px; }
  .page--right .page__footer { left: 3px; }
  .footer__org, .footer__issue {
    position: absolute; top: 0; height: 16px;
    font-family: "PT Sans Narrow", "Arial Narrow", sans-serif;
    font-weight: 700; font-size: 11px;
    line-height: 16px; letter-spacing: 0.6px;
    color: var(--white);
  }
  .footer__org { left: 28px; }
  .footer__issue {
    right: 0; width: 240px;
    background: var(--brick);
    clip-path: polygon(16px 0, 100% 0, 100% 100%, 0 100%);
    text-align: right; padding-right: 44px;
  }
</style>
</head>
<body>
<main class="spread">

  <section class="page page--left">
    <div class="page__top-band"></div>
    <div class="page__body">
      <div class="intro">
        <p>Phasellus viverra nulla ut metus varius laoreet. Quisque rutrum. Aenean imperdiet. Etiam ultricies nisi vel augue. Curabitur ullamcorper ultricies nisi. Nam eget dui. Etiam rhoncus. Maecenas tempus, tellus eget condimentum rhoncus, sem quam semper libero, sit amet adipiscing sem neque sed ipsum.</p>
        <p>Nam quam nunc, blandit vel, luctus pulvinar, hendrerit id, lorem. Maecenas nec odio et ante tincidunt tempus. Donec vitae sapien ut libero venenatis faucibus. Nullam quis ante. Etiam sit amet orci eget eros faucibus tincidunt. Duis leo. Sed fringilla mauris sit amet nibh. Donec sodales sagittis magna.</p>
        <p>Sed consequat, leo eget bibendum sodales, augue velit cursus nunc, quis gravida magna mi a libero. Fusce vulputate eleifend sapien. Vestibulum purus quam, scelerisque ut, mollis sed, nonummy id, metus. Nullam accumsan lorem in dui. Cras ultricies mi eu turpis hendrerit fringilla. Vestibulum ante ipsum primis in faucibus orci luctus et ultrices posuere cubilia Curae; In ac dui quis mi</p>
      </div>

      <h2 class="article-title">THIS IS DUMMY TITLE 03 GENERATED</h2>
      <p>Lorem ipsum dolor sit amet, consectetuer adipiscing elit. Aenean commodo ligula eget dolor. Aenean massa. Cum sociis natoque penatibus et magnis dis parturient montes, nascetur ridiculus mus. Donec quam felis, ultricies nec, pellentesque eu, pretium quis, sem.</p>
      <p>Nulla consequat massa quis enim. Donec pede justo, fringilla vel, aliquet nec, vulputate eget, arcu. In enim justo, rhoncus ut, imperdiet a, venenatis vitae, justo. Nullam dictum felis eu pede mollis pretium. Integer tincidunt. Cras dapibus. Vivamus elementum semper nisi.</p>
      <div class="photo-slot photo-slot--right photo-slot--a" role="img" aria-label="Article photo for title 03">
        <span class="photo-slot__label">Placeholder Image</span>
        <span class="photo-slot__sub">Lorem Ipsum</span>
      </div>
      <p>Aenean vulputate eleifend tellus. Aenean leo ligula, porttitor eu, consequat vitae, eleifend ac, enim. Aliquam lorem ante, dapibus in, viverra quis, feugiat a, tellus. Phasellus viverra nulla ut metus varius laoreet. Quisque rutrum. Aenean imperdiet. Etiam ultricies nisi vel augue.</p>
      <p>Curabitur ullamcorper ultricies nisi. Nam eget dui. Etiam rhoncus. Maecenas tempus, tellus eget condimentum rhoncus, sem quam semper libero, sit amet adipiscing sem neque sed ipsum. Nam quam nunc, blandit vel, luctus pulvinar, hendrerit id, lorem. Maecenas nec odio et ante tincidunt tempus. Donec vitae sapien ut libero venenatis faucibus. Nullam quis ante. Etiam sit amet orci eget eros faucibus tincidunt. Duis leo. Sed fringilla mauris sit amet nibh. Donec sodales sagittis magna. Sed consequat, leo eget bibendum sodales, augue velit cursus nunc, quis gravida magna mi a libero.</p>
      <div class="clear"></div>
      <p>Fusce vulputate eleifend sapien. Vestibulum purus quam, scelerisque ut, mollis sed, nonummy id, metus. Nullam accumsan lorem in dui. Cras ultricies mi eu turpis hendrerit fringilla. Vestibulum ante ipsum primis in faucibus orci luctus et ultrices posuere cubilia Curae; In ac dui quis mi consectetuer lacinia. Nam pretium turpis et arcu. Duis arcu tortor, suscipit eget, imperdiet nec, imperdiet iaculis, ipsum. Sed aliquam ultrices mauris. Integer ante arcu, accumsan a, consectetuer eget, posuere ut, mauris.</p>
      <p>Praesent adipiscing. Phasellus ullamcorper ipsum rutrum nunc. Nunc nonummy metus. Vestibulum volutpat pretium libero. Cras id dui. Aenean ut eros et nisl sagittis vestibulum. Nullam nulla eros, ultricies sit amet, nonummy id, imperdiet feugiat, pede. Sed lectus. Donec mollis hendrerit risus. Phasellus nec sem in justo pellentesque facilisis. Etiam imperdiet imperdiet orci. Nunc nec neque. Phasellus leo dolor, tempus non, auctor et, hendrerit quis, nisi. Curabitur ligula sapien, tincidunt non, euismod vitae, posuere imperdiet, leo.</p>
      <p>Maecenas malesuada. Praesent congue erat at massa. Sed cursus turpis vitae tortor. Donec posuere vulputate arcu. Phasellus accumsan cursus velit. Vestibulum ante ipsum primis in faucibus orci luctus et ultrices posuere cubilia Curae; Sed aliquam, nisi quis porttitor congue, elit erat euismod orci, ac</p>
    </div>
    <footer class="page__footer">
      <span class="footer__org">GUILD OF ACUTE PRACTICE MEDICINE</span>
      <span class="footer__issue">VOLUME - 01 | ISSUE - 001</span>
    </footer>
  </section>

  <section class="page page--right">
    <div class="page__top-band"></div>
    <div class="page__body">
      <h2 class="article-title">THIS IS DUMMY TITLE 04 GENERATED</h2>
      <div class="photo-slot photo-slot--left photo-slot--b" role="img" aria-label="Article photo for title 04">
        <span class="photo-slot__label">Placeholder Image</span>
        <span class="photo-slot__sub">Lorem Ipsum</span>
      </div>
      <p>Lorem ipsum dolor sit amet, consectetuer adipiscing elit. Aenean commodo ligula eget dolor. Aenean massa. Cum sociis natoque penatibus et magnis dis parturient montes, nascetur ridiculus mus.</p>
      <p>Donec quam felis, ultricies nec, pellentesque eu, pretium quis, sem. Nulla consequat massa quis enim. Donec pede justo, fringilla vel, aliquet nec, vulputate eget, arcu. In enim justo, rhoncus ut, imperdiet a, venenatis vitae, justo. Nullam dictum felis eu pede mollis pretium. Integer tincidunt. Cras dapibus. Vivamus elementum semper nisi. Aenean vulputate eleifend tellus. Aenean leo ligula, porttitor eu, consequat vitae, eleifend ac, enim.</p>
      <p>Aliquam lorem ante, dapibus in, viverra quis, feugiat a, tellus. Phasellus viverra nulla ut metus varius laoreet. Quisque rutrum. Aenean imperdiet. Etiam ultricies nisi vel augue. Curabitur ullamcorper ultricies nisi. Nam eget dui. Etiam rhoncus. Maecenas tempus, tellus eget condimentum rhoncus, sem quam semper libero, sit amet adipiscing sem neque sed ipsum. Nam quam nunc, blandit vel, luctus pulvinar, hendrerit id, lorem. Maecenas nec odio et ante tincidunt tempus. Donec vitae sapien ut libero venenatis faucibus. Nullam quis ante. Etiam sit amet orci eget eros faucibus tincidunt.</p>
      <p>Duis leo. Sed fringilla mauris sit amet nibh. Donec sodales sagittis magna. Sed consequat, leo eget bibendum sodales, augue velit cursus nunc, quis gravida magna mi a libero. Fusce vulputate eleifend sapien. Vestibulum purus quam, scelerisque ut, mollis sed, nonummy id, metus. Nullam accumsan lorem in dui. Cras ultricies mi eu turpis hendrerit fringilla. Vestibulum ante ipsum primis in faucibus orci luctus et ultrices posuere cubilia Curae; In ac dui quis mi consectetuer lacinia. Nam pretium turpis et arcu. Duis arcu tortor, suscipit eget, imperdiet nec, imperdiet iaculis, ipsum. Sed aliquam ultrices mauris. Integer ante arcu, accumsan</p>
      <div class="clear"></div>

      <h2 class="article-title" style="margin-top:14px">THIS IS DUMMY TITLE 05 GENERATED</h2>
      <div class="photo-slot photo-slot--right photo-slot--c" role="img" aria-label="Article photo for title 05">
        <span class="photo-slot__label">Placeholder Image</span>
        <span class="photo-slot__sub">Lorem Ipsum</span>
      </div>
      <p>Lorem ipsum dolor sit amet, consectetuer adipiscing elit. Aenean commodo ligula eget dolor. Aenean massa. Cum sociis natoque penatibus et magnis dis parturient montes, nascetur ridiculus mus.</p>
      <p>Donec quam felis, ultricies nec, pellentesque eu, pretium quis, sem. Nulla consequat massa quis enim. Donec pede justo, fringilla vel, aliquet nec, vulputate eget, arcu. In enim justo, rhoncus ut, imperdiet a, venenatis vitae, justo. Nullam dictum felis eu pede mollis pretium. Integer tincidunt. Cras dapibus.</p>
      <p>Vivamus elementum semper nisi. Aenean vulputate eleifend tellus. Aenean leo ligula, porttitor eu, consequat vitae, eleifend ac, enim. Aliquam lorem ante, dapibus in, viverra quis, feugiat a, tellus. Phasellus viverra nulla ut metus varius laoreet. Quisque rutrum. Aenean imperdiet. Etiam ultricies nisi vel augue. Curabitur ullamcorper ultricies nisi. Nam eget dui. Etiam rhoncus. Maecenas tempus, tellus eget condimentum rhoncus, sem quam semper libero, sit amet adipiscing sem neque sed ipsum. Nam quam nunc, blandit vel, luctus pulvinar, hendrerit id,</p>
      <div class="clear"></div>
      <p>lorem. Maecenas nec odio et ante tincidunt tempus. Donec vitae sapien ut libero venenatis faucibus. Nullam quis ante. Etiam sit amet orci eget eros faucibus tincidunt. Duis leo. Sed fringilla mauris sit amet nibh. Donec sodales sagittis magna. Sed consequat, leo eget bibendum sodales, augue velit cursus nunc, quis gravida magna mi a libero. Fusce vulputate eleifend sapien. Vestibulum purus quam, scelerisque ut, mollis sed, nonummy id, metus. Nullam accumsan lorem in dui. Cras ultricies mi eu turpis hendrerit fringilla. Vestibulum ante ipsum primis in faucibus orci luctus et ultrices posuere cubilia Curae; In ac dui quis mix.</p>
    </div>
    <footer class="page__footer">
      <span class="footer__org">GUILD OF ACUTE PRACTICE MEDICINE</span>
      <span class="footer__issue">VOLUME - 01 | ISSUE - 001</span>
    </footer>
  </section>

</main>
</body>
</html>
```